Stylish Business Cards Wanted

- DOUBLE SIDED Design Required -

High end, edgy cards for a corporate and personal stylist. Must include logo,
Name: Belinda Harwick
Title: Director and Stylist
telephone : +61 8 7142 5809
email: belinda@theloombriefing.example
website: theloombriefing.example
Tag: Corporate Workwear & Uniform Specialist | Personal Stylist
Would like nice icons for telephone, email, website

Target Market(s)

Businesses wanting stylish uniforms, people wanting stylish wardrobes

Industry/Entity Type

Corporate Workwear Stylist

Contact Information for Business Card

I would like black, white and gold foiling incorporated in the design - possibly a touch of the other colours on my branding guide attached Name: Belinda Harwick Title: Director and Stylist telephone : +61 8 7142 5809 email: belinda@theloombriefing.example website: theloombriefing.example Tag: Corporate Workwear & Uniform Specialist | Personal Stylist Would like nice icons for telephone, email, website

Font styles to use
Other font styles liked:
• Raleway

Colors

Designer to choose colors to be used in the design.

Requirements
Must have
• Gold foil accents

```html
<!DOCTYPE html>
<html lang="en">
<head>
<meta charset="utf-8">
<title>The Loom Briefing – Business Cards</title>
<link href="https://fonts.googleapis.com/css2?family=Montserrat:wght@600&family=Arimo:wght@400&display=swap" rel="stylesheet">
<style>
  :root {
    --backdrop: #1f1f1f;
    --card: #0b0b0b;
    --ink-white: #eef0ee;
    --gold: #e2b43c;
    --divider: #2e2e2e;
  }
  * { box-sizing: border-box; margin: 0; padding: 0; }
  html, body { width: 1200px; height: 900px; overflow: hidden; }
  body {
    background: var(--backdrop);
    font-family: "Arimo", Arial, sans-serif;
    color: var(--ink-white);
    display: flex;
    flex-direction: column;
    align-items: center;
    justify-content: center;
    gap: 52px;
  }
  .card {
    width: 640px;
    height: 366px;
    background: var(--card);
    border-radius: 3px;
    position: relative;
    box-shadow: 0 14px 30px rgba(0,0,0,.55);
  }
  .brand-name {
    font-family: "Arimo", Arial, sans-serif;
    font-weight: 400;
    color: var(--ink-white);
    line-height: 1.05;
    text-align: center;
  }

  /* Front: brand + tagline */
  .card-front .brand-name {
    position: absolute;
    left: 0; right: 0;
    top: 112px;
    font-size: 54px;
  }
  .tagline {
    position: absolute;
    left: 0; right: 0;
    bottom: 54px;
    text-align: center;
    font-size: 17px;
    letter-spacing: .2px;
  }
  .tagline .dot {
    display: inline-block;
    width: 7px; height: 7px;
    border-radius: 50%;
    background: var(--gold);
    margin: 0 12px;
    vertical-align: middle;
  }

  /* Back: brand + contact */
  .card-back { display: flex; }
  .card-back .brand-panel {
    width: 290px;
    display: flex;
    align-items: center;
    justify-content: center;
    padding: 0 24px;
  }
  .card-back .brand-name { font-size: 40px; }
  .card-back .rule {
    width: 1px;
    background: var(--divider);
    margin: 70px 0 60px;
  }
  .contact-panel {
    flex: 1;
    padding: 90px 0 0 40px;
  }
  .person-name {
    font-family: "Montserrat", Arial, sans-serif;
    font-weight: 600;
    font-size: 25px;
    color: var(--gold);
    letter-spacing: .3px;
    text-transform: uppercase;
  }
  .person-title { font-size: 17px; margin-top: 4px; }
  .contact-list { list-style: none; margin-top: 40px; }
  .contact-list li {
    display: flex;
    align-items: center;
    gap: 12px;
    font-size: 17px;
    line-height: 27px;
  }
  .contact-list svg { width: 16px; height: 16px; flex: none; fill: var(--gold); }
</style>
</head>
<body>

  <section class="card card-front">
    <p class="brand-name">The Loom<br>Briefing</p>
    <p class="tagline">Corporate Workwear &amp; Uniform Specialist<span class="dot"></span>Personal Stylist</p>
  </section>

  <section class="card card-back">
    <div class="brand-panel">
      <p class="brand-name">The Loom<br>Briefing</p>
    </div>
    <div class="rule"></div>
    <div class="contact-panel">
      <h1 class="person-name">Belinda Harwick</h1>
      <p class="person-title">Director and Stylist</p>
      <ul class="contact-list">
        <li>
          <svg viewBox="0 0 24 24" aria-hidden="true"><path d="M6.6 10.8a15.1 15.1 0 0 0 6.6 6.6l2.2-2.2a1 1 0 0 1 1-.25 11.4 11.4 0 0 0 3.6.57 1 1 0 0 1 1 1V20a1 1 0 0 1-1 1A17 17 0 0 1 3 4a1 1 0 0 1 1-1h3.5a1 1 0 0 1 1 1c0 1.25.2 2.45.57 3.57a1 1 0 0 1-.25 1z"/></svg>
          +61 8 7142 5809
        </li>
        <li>
          <svg viewBox="0 0 24 24" aria-hidden="true"><path d="M2 5h20v14H2zm2 2v.4l8 5.2 8-5.2V7zm0 2.8V17h16V9.8l-8 5.2z"/></svg>
          belinda@theloombriefing.example
        </li>
        <li>
          <svg viewBox="0 0 24 24" aria-hidden="true"><path d="M12 2a10 10 0 1 0 0 20 10 10 0 0 0 0-20zm6.9 6h-2.9a15.6 15.6 0 0 0-1.4-3.6A8 8 0 0 1 18.9 8zM12 4c.8 1.2 1.5 2.5 1.9 4h-3.8c.4-1.5 1.1-2.8 1.9-4zM4.3 14a8 8 0 0 1 0-4h3.4a16 16 0 0 0 0 4zm.8 2h2.9c.3 1.3.8 2.5 1.4 3.6A8 8 0 0 1 5.1 16zM8 8H5.1a8 8 0 0 1 4.3-3.6C8.8 5.5 8.3 6.7 8 8zm4 12c-.8-1.2-1.5-2.5-1.9-4h3.8c-.4 1.5-1.1 2.8-1.9 4zm2.3-6H9.7a14.7 14.7 0 0 1 0-4h4.6a14.7 14.7 0 0 1 0 4zm.3 5.6c.6-1.1 1.1-2.3 1.4-3.6h2.9a8 8 0 0 1-4.3 3.6zm1.7-5.6a16 16 0 0 0 0-4h3.4a8 8 0 0 1 0 4z"/></svg>
          theloombriefing.example
        </li>
      </ul>
    </div>
  </section>

</body>
</html>
```